Tech business card design

We need an amazing business card design for our new business 'Pexla' a marketing tech startup based in Sydney, Australia. We provide an online marketplace for businesses to search and buy advertising media, connect with service providers and learn more about marketing. We wish to communicate 'cool tech', reliability and professionalism and design based around our logo.

Target Market(s)

Business Owners

Contact Information for Business Card

Name
Position
Email Address
Website
Phone Number

Font styles to use
Other font styles liked:
• Avenir & Avenir Next

Colors

Designer to choose colors to be used in the design.

```html
<!DOCTYPE html>
<html lang="en">
<head>
<meta charset="utf-8">
<title>Pexla Business Card</title>
<link href="https://fonts.googleapis.com/css2?family=Nunito+Sans:wght@400;700;800&display=swap" rel="stylesheet">
<style>
  :root {
    --canvas-bg: #e9e9ec;
    --brand-blue: #3b3aa6;
    --brand-navy: #1b1d4b;
    --card-white: #ffffff;
    --text-grey: #4a4a5a;
    --rule-navy: #2a2a6a;
  }
  * { margin: 0; padding: 0; box-sizing: border-box; }
  html, body { width: 1200px; height: 900px; overflow: hidden; }
  body {
    background: var(--canvas-bg);
    font-family: "Nunito Sans", Arial, sans-serif;
    position: relative;
  }
  .card {
    position: absolute;
    left: 260px;
    width: 680px;
    height: 388px;
    box-shadow: 0 6px 18px rgba(0,0,0,0.18);
    overflow: hidden;
  }
  .card-front { top: 44px; }
  .card-back { top: 468px; background: var(--card-white); }

  .front-texture {
    position: absolute; inset: 0;
    background: linear-gradient(160deg, #4141b0 0%, var(--brand-blue) 55%, #34339a 100%);
  }
  .front-wordmark {
    position: absolute;
    right: 28px; bottom: 48px;
    font-weight: 800;
    font-size: 132px;
    line-height: 1;
    letter-spacing: -2px;
    color: var(--brand-navy);
  }

  .back-wordmark {
    position: absolute;
    left: 40px; top: 150px;
    font-weight: 800;
    font-size: 118px;
    line-height: 1;
    letter-spacing: -2px;
    color: var(--brand-navy);
  }
  .identity {
    position: absolute;
    left: 400px; top: 56px;
  }
  .identity-name {
    font-weight: 800;
    font-size: 21px;
    letter-spacing: 0.5px;
    color: var(--brand-navy);
  }
  .identity-role {
    font-weight: 700;
    font-size: 14px;
    color: var(--text-grey);
    margin-top: 2px;
  }
  .identity-rule {
    position: absolute;
    left: 400px; right: 0; top: 114px;
    height: 2px;
    background: var(--rule-navy);
  }
  .contact-list {
    position: absolute;
    left: 420px; top: 140px;
    list-style: none;
  }
  .contact-item {
    display: flex;
    align-items: center;
    gap: 10px;
    font-size: 15px;
    color: var(--text-grey);
    height: 24px;
  }
  .contact-item svg { width: 14px; height: 14px; fill: var(--brand-navy); flex: none; }
  .address {
    position: absolute;
    right: 40px; bottom: 42px;
    font-size: 15px;
    color: var(--text-grey);
  }
</style>
</head>
<body>
  <section class="card card-front">
    <div class="front-texture" role="img" aria-label="Blue textured linen pattern background"></div>
    <div class="front-wordmark">Pexla</div>
  </section>

  <section class="card card-back">
    <div class="back-wordmark">Pexla</div>

    <div class="identity">
      <div class="identity-name">JOHN SMITH</div>
      <div class="identity-role">Position</div>
    </div>
    <div class="identity-rule"></div>

    <ul class="contact-list">
      <li class="contact-item">
        <svg viewBox="0 0 24 24"><path d="M6.6 10.8a15.1 15.1 0 0 0 6.6 6.6l2.2-2.2a1 1 0 0 1 1-.25 11.4 11.4 0 0 0 3.6.57 1 1 0 0 1 1 1V20a1 1 0 0 1-1 1A17 17 0 0 1 3 4a1 1 0 0 1 1-1h3.5a1 1 0 0 1 1 1c0 1.25.2 2.45.57 3.6a1 1 0 0 1-.25 1z"/></svg>
        012-345-6789
      </li>
      <li class="contact-item">
        <svg viewBox="0 0 24 24"><path d="M2 5h20v14H2z M4 7v.5l8 5 8-5V7l-8 5z" fill-rule="evenodd"/></svg>
        info@pexla.com
      </li>
      <li class="contact-item">
        <svg viewBox="0 0 24 24"><path d="M12 2a10 10 0 1 0 0 20 10 10 0 0 0 0-20zm6.9 9h-3a15 15 0 0 0-1.2-5.6A8 8 0 0 1 18.9 11zM12 4c.9 1.3 1.7 3.8 1.9 7h-3.8c.2-3.2 1-5.7 1.9-7zM4.1 13h3a15 15 0 0 0 1.2 5.6A8 8 0 0 1 4.1 13zm3-2h-3a8 8 0 0 1 4.2-5.6A15 15 0 0 0 7.1 11zM12 20c-.9-1.3-1.7-3.8-1.9-7h3.8c-.2 3.2-1 5.7-1.9 7zm2.7-1.4a15 15 0 0 0 1.2-5.6h3a8 8 0 0 1-4.2 5.6z"/></svg>
        www.pexla.com
      </li>
    </ul>

    <div class="address">Street Name, City Name, Zipcode 012345</div>
  </section>
</body>
</html>
```